Logo + Label Design (Men’s Grooming Brand & Product Packaging)

Design a logo and 2 oz pomade label for Brel, a modern men’s grooming brand focused on clean, high-quality, natural ingredients. The design should establish a bold, masculine, minimalist identity that can later extend to products like shaving gel and body wash.

Key Requirements

Create a primary logo for “Brel” and a core label for the 2 oz pomade jar (screw-top).

Use a clean, modern style — masculine, confident, and approachable (think Dorran’s, Velta, Northfield Kit).

Design for 1–2 color screen printing on solid jar colors (white, black, or navy).

Avoid gradients, foil, or embossing. Must work in black & white.

Provide: vector logo, mockup of the 2 oz jar, color palette (CMYK/RGB/HEX), and font specs.

Winning design may lead to future projects (body wash, shave gel, skincare lines).

Font styles to use
Other font styles liked:
• We like the fonts and design concept in the attached mockup.

Requirements
Should not have
• We want to avoid too much writing or busy designs. We want to avoid having graphics/illustrations embedded in the logo if they will cause the brand to look less classy or sophisticated. We also want the design to look simple and all-American (e.g. Hollister and Vane, Pine Ledger, The KIM, etc). We’d like to give a Pellham & Royce vibe that feels classy and high end.

```html
<!DOCTYPE html>
<html lang="en">
<head>
<meta charset="utf-8">
<title>Brel Hair Pomade – Label System</title>
<link rel="stylesheet" href="https://fonts.googleapis.com/css2?family=Work+Sans:wght@700&family=Questrial&family=Montserrat:wght@800&family=Arimo:wght@400&display=swap">
<style>
  :root {
    --ink: #000000;
    --paper: #ffffff;
    --backdrop: #abaa9f;
  }
  * { margin: 0; padding: 0; box-sizing: border-box; }
  html, body { width: 1200px; height: 1200px; overflow: hidden; }
  body { background: var(--backdrop); position: relative; font-family: "Arimo", sans-serif; }

  .wrap-label {
    position: absolute; left: 26px; top: 330px;
    width: 1148px; height: 136px;
    display: flex; background: var(--paper);
  }
  .wrap-label__dark {
    width: 673px; background: var(--ink); color: var(--paper);
    display: flex; align-items: center; justify-content: space-between;
    padding: 0 10px 0 12px;
  }
  .directions {
    width: 427px; font-family: "Arimo", sans-serif; font-size: 12.2px;
    line-height: 15.6px; text-align: justify; text-transform: uppercase;
    letter-spacing: 0.2px;
  }
  .wordmark {
    font-family: "Work Sans", sans-serif; font-weight: 700;
    font-size: 108px; line-height: 1; letter-spacing: -5px; color: var(--paper);
    margin-top: -8px;
  }
  .wrap-label__light {
    flex: 1; display: flex; padding: 18px 10px 0 6px; color: var(--ink);
  }
  .product-block { width: 220px; }
  .product-type { font-family: "Questrial", sans-serif; font-size: 17.5px; letter-spacing: 1px; white-space: nowrap; }
  .scent { font-family: "Questrial", sans-serif; font-size: 24px; letter-spacing: 1.2px; white-space: nowrap; margin-top: 1px; }
  .hold { font-family: "Montserrat", sans-serif; font-weight: 800; font-size: 10.6px; letter-spacing: 1.1px; white-space: nowrap; margin-top: 6px; }
  .net-wt {
    display: inline-block; background: var(--ink); color: var(--paper);
    font-family: "Arimo", sans-serif; font-size: 10.5px; padding: 2px 6px; margin: 10px 0 0 3px;
  }
  .claims { padding-left: 22px; font-size: 8.2px; line-height: 11px; text-transform: uppercase; }
  .claims ul { list-style: none; margin-top: 6px; }
  .claims li::before { content: "• "; }
  .maker { margin-top: 10px; font-size: 9.6px; line-height: 11.4px; }

  .lid-label { position: absolute; left: 390px; top: 550px; width: 420px; height: 420px; }
  .lid-label text { font-family: "Arimo", sans-serif; }
</style>
</head>
<body>

<section class="wrap-label" aria-label="Jar wrap label">
  <div class="wrap-label__dark">
    <p class="directions">Directions:<br>Melt small amount of pomade between hands before massaging into damp hair (for sleeker look) or dry hair (for more texture). Style as desired. For external use only. Avoid contact with eyes. If irritation occurs, discontinue use.</p>
    <h1 class="wordmark">Brel</h1>
  </div>
  <div class="wrap-label__light">
    <div class="product-block">
      <p class="product-type">MEN’S HAIR POMADE</p>
      <p class="scent">FRESH &amp; CLEAN</p>
      <p class="hold">MEDIUM HOLD ● MATTE FINISH</p>
      <span class="net-wt">NET WT 2 OZ (57 G)</span>
    </div>
    <div class="claims">
      <ul>
        <li>Naturally derived plant &amp; bee-based ingredients</li>
        <li>Alcohol free, non-irritating</li>
        <li>Formulated to minimize scalp irritation</li>
      </ul>
      <p class="maker">Manufactured by:<br>Brel Health Products, Millbrook, NC 27999<br>Visit us at brelhealthproducts.com</p>
    </div>
  </div>
</section>

<svg class="lid-label" viewBox="0 0 400 400" aria-label="Jar lid label">
  <defs>
    <clipPath id="inner-disc"><circle cx="200" cy="200" r="155"/></clipPath>
    <path id="ring-path" d="M200,200 m-174,0 a174,174 0 1,1 348,0 a174,174 0 1,1 -348,0"/>
  </defs>
  <circle cx="200" cy="200" r="199" fill="var(--paper)"/>
  <circle cx="200" cy="200" r="191" fill="var(--ink)"/>
  <circle cx="200" cy="200" r="158" fill="var(--paper)"/>
  <g clip-path="url(#inner-disc)">
    <rect x="0" y="0" width="400" height="168" fill="var(--ink)"/>
  </g>
  <text fill="var(--paper)" font-size="10.5" letter-spacing="0.6">
    <textPath href="#ring-path" startOffset="0">www.brelhealthproducts.com • Naturally derived plant &amp; bee-based ingredients • Alcohol free, Non-irritating • Formulated to minimize scalp irritation •</textPath>
  </text>
  <text x="200" y="148" text-anchor="middle" fill="var(--paper)" font-family="Work Sans, sans-serif" font-weight="700" font-size="82" letter-spacing="-4" style="font-family:'Work Sans',sans-serif">Brel</text>
  <text x="200" y="204" text-anchor="middle" fill="var(--ink)" font-size="29" letter-spacing="1" style="font-family:'Questrial',sans-serif;font-weight:700">HAIR POMADE</text>
  <text x="200" y="240" text-anchor="middle" fill="var(--ink)" font-size="26" letter-spacing="1.2" style="font-family:'Questrial',sans-serif">FRESH &amp; CLEAN</text>
  <text x="200" y="268" text-anchor="middle" fill="var(--ink)" font-size="12" letter-spacing="1" style="font-family:'Montserrat',sans-serif;font-weight:800">MEDIUM HOLD ● MATTE FINISH</text>
  <rect x="137" y="282" width="126" height="20" fill="var(--ink)"/>
  <text x="200" y="297" text-anchor="middle" fill="var(--paper)" font-size="12.5">NET WT 2 OZ (57 G)</text>
</svg>

</body>
</html>
```